Dental Practice Billboard Design

We are a newer dental practice in need of a simple but appealing billboard for our growing dental practice to attract new patients. The practice is owned by husband and wife dentists and is family friendly in a small town in Kentucky. We try to be very friendly and caring to our patients. Would prefer a blue background for the billboard and our tooth logo to be prominent. We are partial to the Patua One font used in the image below but please feel free to tweak it as you deem necessary. The shape of the uppercase D and lowercase g are why we like that font, so fonts with a similarly shaped “D” and “g” would work as well. Please include our phone number (555) 847-1390. Please see our website Harlowbrookdentistry.example for more info on the practice if needed. Thank you! Looking forward to seeing your creation.
Updates

The dimensions will be 12ft x 24ft (3.6576m x 7.3152m). Apologies for not including this in the original prompt. Thank you all for your submissions.

Industry/Entity Type

Dental

Font styles to use
Other font styles liked:
• Patua One

Colors
0054AA
0677BA
7BADD7
CADEEF
E8F1F8
0094D4
00A9DD
6FCCEA
C7EBF8
E9F6FB
00AB8E
00BBA5
67D7C9
C6EFE9
E9F9F6
59FF00
82FF00
B8FF75
E3FFCB
F4FFEA

Requirements
Must have
• Phone number, website, Logo, Practice name “Harlow Brook Dentistry”
Should not have
• A tagline or slogan

```html
<!DOCTYPE html>
<html lang="en">
<head>
<meta charset="utf-8">
<title>Harlow Brook Dentistry Billboard</title>
<link rel="stylesheet" href="https://fonts.googleapis.com/css2?family=Patua+One&family=Bitter:wght@700&display=swap">
<style>
  :root {
    --backdrop: #808080;
    --brand-blue: #0054b8;
    --brand-green: #14b317;
    --paper: #ffffff;
  }
  html, body {
    margin: 0;
    padding: 0;
    width: 1200px;
    height: 1059px;
    overflow: hidden;
    background: var(--backdrop);
  }
  .billboard {
    position: absolute;
    left: 201px;
    top: 330px;
    width: 797px;
    height: 399px;
    overflow: hidden;
    background: var(--paper);
  }
  .billboard-shapes {
    position: absolute;
    inset: 0;
  }
  .practice-name {
    position: absolute;
    left: 38px;
    top: 28px;
    margin: 0;
    font-family: "Patua One", serif;
    font-weight: 400;
    line-height: 1;
  }
  .practice-name .name-primary {
    display: block;
    font-size: 112px;
    color: var(--brand-green);
    letter-spacing: -1px;
  }
  .practice-name .name-secondary {
    display: block;
    margin-top: 2px;
    font-size: 48px;
    color: var(--paper);
  }
  .contact-line {
    position: absolute;
    left: 34px;
    display: flex;
    align-items: center;
    gap: 14px;
    font-family: "Bitter", serif;
    font-weight: 700;
    color: var(--paper);
  }
  .contact-phone {
    top: 232px;
    font-size: 40px;
    letter-spacing: 1px;
  }
  .contact-web {
    top: 290px;
    font-size: 23px;
    letter-spacing: 1.4px;
  }
  .contact-icon {
    flex: none;
  }
  .office-hours {
    position: absolute;
    left: 32px;
    top: 348px;
    display: flex;
    align-items: center;
    gap: 10px;
    font-family: "Bitter", serif;
    font-weight: 700;
  }
  .office-hours-label {
    font-size: 18px;
    color: var(--brand-blue);
    letter-spacing: 0.5px;
  }
  .office-hours-times {
    font-size: 16px;
    line-height: 21px;
    color: var(--paper);
    letter-spacing: 1.1px;
  }
  .logo-name {
    position: absolute;
    left: 520px;
    top: 130px;
    width: 260px;
    text-align: center;
    font-family: "Patua One", serif;
    font-size: 50px;
    line-height: 1.05;
    color: var(--brand-blue);
  }
  .logo-dot {
    display: block;
    width: 34px;
    height: 34px;
    margin: 0 auto 12px;
    border-radius: 50%;
    background: var(--brand-green);
  }
</style>
</head>
<body>
  <section class="billboard">
    <svg class="billboard-shapes" width="797" height="399" viewBox="0 0 797 399" aria-hidden="true">
      <path d="M0 0 H481 C455 0 446 20 446 40 C446 62 462 76 472 82 C462 110 458 130 458 160 C458 210 490 300 520 340 C535 372 552 392 569 399 H0 Z" fill="var(--brand-blue)"/>
      <path d="M0 343 H523 C537 370 552 392 569 399 H0 Z" fill="var(--brand-green)"/>
    </svg>

    <h1 class="practice-name">
      <span class="name-primary">Harlow</span>
      <span class="name-secondary">Brook Dentistry</span>
    </h1>

    <div class="contact-line contact-phone">
      <svg class="contact-icon" width="32" height="32" viewBox="0 0 24 24" aria-hidden="true">
        <path fill="var(--brand-green)" d="M6.6 10.8c1.4 2.8 3.8 5.1 6.6 6.6l2.2-2.2c.3-.3.7-.4 1-.2 1.1.4 2.3.6 3.6.6.6 0 1 .4 1 1V20c0 .6-.4 1-1 1C10.6 21 3 13.4 3 4c0-.6.4-1 1-1h3.5c.6 0 1 .4 1 1 0 1.3.2 2.5.6 3.6.1.3 0 .7-.2 1z"/>
        <path fill="none" stroke="var(--brand-green)" stroke-width="1.6" stroke-linecap="round" d="M14 3.5a7 7 0 0 1 6.5 6.5M14 7a3.5 3.5 0 0 1 3 3"/>
      </svg>
      <span>(555) 847-1390</span>
    </div>

    <div class="contact-line contact-web">
      <svg class="contact-icon" width="27" height="27" viewBox="0 0 24 24" aria-hidden="true">
        <g fill="none" stroke="var(--brand-green)" stroke-width="1.6">
          <circle cx="12" cy="12" r="10"/>
          <ellipse cx="12" cy="12" rx="4.5" ry="10"/>
          <path d="M2 12h20M4 6.5h16M4 17.5h16M12 2v20"/>
        </g>
      </svg>
      <span>Harlowbrookdentistry.example</span>
    </div>

    <div class="office-hours">
      <span class="office-hours-label">OFFICE HOURS:-</span>
      <span class="office-hours-times">Mon - Tue - Thu - Fri : 8AM - 5PM<br>Sat - Sun - Wed : CLOSED</span>
    </div>

    <div class="logo-name">
      <span class="logo-dot"></span>
      Harlow Brook
    </div>
  </section>
</body>
</html>
```